Optimization existing Business Card

I need a revision of the business card, incl. Logo Design. I am a freelancer and have my headquarters in Berlin. I develop business consulting solutions for banks, insurance and StartUp Companies. I want a simple design of the business card. The final design should professionalism and commitment and openness to communicate. I'm open minded in addition to optimizing the existing logo / business card as well on a new idea / proposal for the logo. Idea would be for example the logo of this page: http://dravolt-partners.example.

Target Market(s)

Consulting, Banking, Investment Banking

Industry/Entity Type

Business

Contact Information for Business Card

siehe Anhang (please take a look into the attachments, important)

Font styles to use
Sans Serif

Requirements
Must have
• Please look at my specifications exactly !! (Please see my specifications), CEO Founder not
Should not have
• No gradient !! (No overarching color gradient)

```html
<!DOCTYPE html>
<html lang="de">
<head>
<meta charset="utf-8">
<title>harlenberg consulting – Visitenkarte</title>
<link rel="stylesheet" href="https://fonts.googleapis.com/css2?family=Open+Sans:wght@400;700&family=Carlito&family=Arimo&display=swap">
<style>
  :root {
    --navy: #0d2a52;
    --sky: #1ea5de;
    --ink: #1a1a1a;
    --paper: #ffffff;
  }
  * { margin: 0; padding: 0; box-sizing: border-box; }
  html, body { width: 1200px; height: 806px; overflow: hidden; background: var(--paper); }
  .card { position: relative; width: 1200px; height: 806px; background: var(--paper); overflow: hidden; }
  .card__shapes { position: absolute; inset: 0; }

  .brand { position: absolute; left: 72px; top: 121px; display: flex; align-items: center; }
  .brand__dot { width: 116px; height: 116px; border-radius: 50%; background: var(--navy); flex: none; }
  .brand__name {
    margin-left: 22px; font-family: "Open Sans", sans-serif; font-weight: 700;
    font-size: 44px; line-height: 50px; color: var(--navy); letter-spacing: -0.5px;
  }
  .brand__divider { position: absolute; left: 469px; top: 15px; width: 3px; height: 101px; background: var(--sky); }
  .brand__services {
    position: absolute; left: 485px; top: 18px; list-style: none;
    font-family: "Arimo", sans-serif; font-size: 20px; line-height: 29px; color: var(--navy);
    white-space: nowrap;
  }

  .person { position: absolute; right: 70px; top: 390px; text-align: right; }
  .person__name { font-family: "Open Sans", sans-serif; font-weight: 700; font-size: 32px; color: var(--sky); line-height: 44px; }
  .person__role { font-family: "Open Sans", sans-serif; font-size: 25px; color: var(--ink); line-height: 40px; margin-top: 4px; }

  .contacts { position: absolute; left: 72px; top: 526px; list-style: none; font-family: "Carlito", sans-serif; font-size: 28px; color: var(--ink); }
  .contacts__item { display: flex; align-items: center; height: 41.5px; }
  .contacts__icon { width: 26px; height: 26px; margin-right: 22px; fill: var(--sky); flex: none; }

  .website {
    position: absolute; right: 70px; top: 716px; font-family: "Open Sans", sans-serif;
    font-size: 26px; color: var(--paper); line-height: 38px;
  }
</style>
</head>
<body>
<main class="card">
  <svg class="card__shapes" width="1200" height="806" viewBox="0 0 1200 806" aria-hidden="true">
    <path class="swoosh" fill="var(--sky)" d="M162 703 Q 760 668 1200 572 L 1200 624 Q 760 694 162 703 Z"/>
    <path class="footer-band" fill="var(--navy)" d="M0 711 L 690 711 Q 1000 694 1200 638 L 1200 806 L 0 806 Z"/>
  </svg>

  <header class="brand">
    <div class="brand__dot"></div>
    <div class="brand__name">harlenberg<br>consulting</div>
    <div class="brand__divider"></div>
    <ul class="brand__services">
      <li>UNTERNEHMENSBERATUNG</li>
      <li>BANKING</li>
      <li>BUSINESS COACHING</li>
    </ul>
  </header>

  <section class="person">
    <h1 class="person__name">Tobias Harlenberg</h1>
    <p class="person__role">Management Consultant</p>
  </section>

  <ul class="contacts">
    <li class="contacts__item">
      <svg class="contacts__icon" viewBox="0 0 24 24"><path d="M6.6 10.8a15.2 15.2 0 0 0 6.6 6.6l2.2-2.2c.3-.3.7-.4 1-.2 1.1.4 2.3.6 3.6.6.6 0 1 .4 1 1V20c0 .6-.4 1-1 1A17 17 0 0 1 3 4c0-.6.4-1 1-1h3.5c.6 0 1 .4 1 1 0 1.3.2 2.5.6 3.6.1.3 0 .7-.2 1z"/></svg>
      <span>+49 (0) 30 55501234</span>
    </li>
    <li class="contacts__item">
      <svg class="contacts__icon" viewBox="0 0 24 24"><path d="M8 1h8a2 2 0 0 1 2 2v18a2 2 0 0 1-2 2H8a2 2 0 0 1-2-2V3a2 2 0 0 1 2-2zm0 3v8h8V4zm1 10v2h2v-2zm4 0v2h2v-2zm-4 3v2h2v-2zm4 0v2h2v-2z"/></svg>
      <span>+49 (0) 176 55509876</span>
    </li>
    <li class="contacts__item">
      <svg class="contacts__icon" viewBox="0 0 24 24"><path d="M2 5h20v14H2zm1.5 1.5v.3l8.5 6 8.5-6v-.3zm0 2.2v8.8h17V8.7l-8.5 6z"/></svg>
      <span>tha@harlenberg-consulting.example</span>
    </li>
  </ul>

  <p class="website">www.harlenberg-consulting.example</p>
</main>
</body>
</html>
```